New Baby Formula Company Needs a Shopify Website Design

We are launching a baby formula company and need a Shopify website design. We have a patented product that is a disposable pouch with a frangible seal through the middle. The top half contains formula powder and the bottom half contains purified water. There is also a bottle nipple on the corner under the cap in order to feed the baby. You just need to squeeze the bottom half of the pouch to break the seal and then the water and formula will mix. You then only need to shake it and then remove the cap and feed the baby. We will also sell formula in containers like the other formula companies. We want this website to stand out and look professional. We don't want a boring layout, but something unique and captivating. I have attached a mockup rendering of our product, though it's not the finished product and our logo. This will let you know the color scheme we are going for. Let me know if you have any further questions. Thank you

```html
<!DOCTYPE html>
<html lang="en">
<head>
<meta charset="utf-8">
<title>Nestling – Baby Formula</title>
<link href="https://fonts.googleapis.com/css2?family=Montserrat:wght@400;500;600;700&display=swap" rel="stylesheet">
<style>
:root{
  --green:#9fb338;
  --green-dark:#8aa02a;
  --ink:#1c1c1c;
  --muted:#555;
  --light:#f4f4f4;
  --line:#ddd;
  --white:#fff;
}
*{box-sizing:border-box;margin:0;padding:0}
html,body{width:1200px;height:4026px;overflow:hidden}
body{font-family:'Montserrat',sans-serif;color:var(--ink);background:var(--white);position:relative}
.abs{position:absolute}
a{color:inherit;text-decoration:none}
.btn{display:inline-block;background:var(--green);color:#fff;font-weight:600;border-radius:4px;text-transform:uppercase}

.topbar{top:0;left:0;width:1200px;height:59px;background:var(--light);font-size:15px;font-weight:500;color:#333;display:flex;align-items:center;padding-left:110px}
.topbar .sep{margin:0 18px}
.topbar .icons{position:absolute;right:110px;top:18px;display:flex;gap:28px}

.header{top:59px;left:0;width:1200px;height:104px;background:#fff}
.logo{left:113px;top:68px;width:124px;height:124px;border-radius:50%;background:#fff;z-index:3;display:flex;align-items:center;justify-content:center;border:3px solid var(--green);box-shadow:0 0 0 6px #fff}
.logo span{font-size:22px;font-weight:600;color:var(--green)}
.search{left:701px;top:90px;width:256px;height:40px;border:2px solid #ccc;border-radius:3px;font-size:10px;font-weight:600;padding:12px 10px;color:#333}
.search i{position:absolute;right:-2px;top:-2px;width:36px;height:40px;background:#111;border-radius:3px;display:flex;align-items:center;justify-content:center}
.usd{left:993px;top:103px;font-size:12px;font-weight:600}
.cart{left:1062px;top:95px}

.nav{top:163px;left:0;width:1200px;height:64px;background:var(--green);display:flex;align-items:center;padding-left:267px;gap:42px;color:#fff;font-size:18px;font-weight:600}

.hero{top:227px;left:0;width:1200px;height:507px;background:
  radial-gradient(ellipse 420px 330px at 820px 260px,#d9a98a 0%,#c9a593 30%,rgba(196,186,205,.85) 55%,rgba(210,204,196,0) 80%),
  linear-gradient(90deg,#f6f3f0 0%,#eee8e2 40%,#d4cbc1 70%,#b9b1a7 100%)}
.hero h1{position:absolute;left:58px;font-size:35px;font-weight:600;line-height:1}
.hero .h1a{top:148px;color:var(--green)}
.hero .h1b{top:210px}
.hero .btn{position:absolute;left:59px;top:284px;width:152px;height:47px;line-height:47px;text-align:center;font-size:18px}

.promo{top:831px;width:475px;height:236px;border:4px solid;border-radius:4px;background:#fff}
.promo .pic{position:absolute;left:50px;top:14px;width:110px;height:200px;border-radius:8px}
.promo .txt{position:absolute;left:230px;top:62px;font-size:17px;font-weight:500;line-height:34px}
.promo .btn{position:absolute;left:230px;top:143px;width:123px;height:36px;line-height:36px;text-align:center;font-size:14px}

.title{left:0;width:1200px;text-align:center;font-size:29px;font-weight:500;color:var(--green)}
.dots{left:555px;width:90px;display:flex;justify-content:space-between}
.dots b{width:36px;height:36px;border-radius:50%;background:var(--green);display:block}

.card{width:235px;height:344px;background:#fff;border:1px solid #e4e4e4;box-shadow:0 1px 5px rgba(0,0,0,.15);border-radius:4px;text-align:center;overflow:hidden}
.card .pic{margin:12px auto 0;width:211px;height:210px;border-radius:3px}
.card hr{border:0;border-top:1px solid #ccc;margin:13px 10px 0}
.card h3{font-size:20px;font-weight:500;color:var(--green);margin-top:22px}
.card p{font-size:16px;font-weight:500;margin-top:16px}

.testi{top:2088px;left:0;width:1200px;height:646px;background:var(--green)}
.testi h2{position:absolute;top:78px;width:1200px;text-align:center;color:#fff;font-size:29px;font-weight:500}
.testi .dots{top:128px}
.testi .dots b{background:#fff}
.quote{position:absolute;top:222px;width:440px;text-align:center;color:#fff}
.quote p{font-size:16px;line-height:34px;opacity:.95}
.quote .q{font-size:44px;font-weight:700;line-height:1;margin-top:14px}
.quote .av{width:82px;height:82px;border-radius:50%;margin:14px auto 0;border:3px solid #fff}
.quote .name{font-size:16px;font-weight:500;margin-top:34px}
.pager{position:absolute;top:2661px;left:562px;display:flex;gap:20px}
.pager i{width:13px;height:13px;border-radius:50%;border:2px solid #fff;display:block}
.pager i:first-child{background:#fff}

.post{top:2952px;width:309px}
.post .pic{height:212px}
.post .date{position:absolute;top:237px;left:0;width:50px;height:50px;background:var(--green);color:#fff;text-align:center;border-radius:3px;font-weight:600;font-size:18px;line-height:1;padding-top:8px}
.post .date small{display:block;font-size:11px;margin-top:3px}
.post h4{position:absolute;top:238px;left:67px;font-size:13px;font-weight:500}
.post p{position:absolute;top:268px;left:67px;width:230px;font-size:12px;line-height:25px;color:#333}
.post .btn{position:absolute;top:356px;left:67px;width:123px;height:36px;line-height:36px;text-align:center;font-size:15px}

.feat{top:3438px;left:0;width:1200px;height:128px;background:var(--light)}
.feat .f{position:absolute;top:38px;display:flex;gap:18px;align-items:center}
.feat h5{font-size:18px;font-weight:600;letter-spacing:.5px}
.feat p{font-size:14px;margin-top:10px;color:#333}

.footer{top:3566px;left:0;width:1200px;height:379px;background:var(--green);color:#fff}
.col{position:absolute;top:98px}
.col h6{font-size:21px;font-weight:500;margin-bottom:24px}
.col li{list-style:none;font-size:16px;line-height:38.5px}
.col .ic{display:inline-block;width:42px}
.totop{left:1140px;top:3870px;width:32px;height:32px;border-radius:50%;background:#fff;display:flex;align-items:center;justify-content:center}
.copy{top:3945px;left:0;width:1200px;height:81px;line-height:81px;text-align:center;font-size:16px;font-weight:500}
</style>
</head>
<body>

<div class="abs topbar">CALL US : +1 888 888 8888<span class="sep">|</span>MAIL US : HELLO@NESTLINGBABY.COM
  <div class="icons">
    <svg width="22" height="22" viewBox="0 0 24 24" fill="none" stroke="#333" stroke-width="1.6"><path d="M10 4h9v16h-9M3 12h11M10 8l4 4-4 4"/></svg>
    <svg width="22" height="22" viewBox="0 0 24 24" fill="none" stroke="#333" stroke-width="1.6"><circle cx="12" cy="8" r="4"/><path d="M4 21c1-5 15-5 16 0"/></svg>
    <svg width="22" height="22" viewBox="0 0 24 24" fill="none" stroke="#333" stroke-width="1.6"><path d="M12 20s-8-5-8-11a4 4 0 0 1 8-1 4 4 0 0 1 8 1c0 6-8 11-8 11z"/></svg>
  </div>
</div>

<div class="abs header"></div>
<div class="abs logo"><span>Nestling</span></div>
<div class="abs search">SEARCH...<i><svg width="16" height="16" viewBox="0 0 24 24" fill="none" stroke="#fff" stroke-width="2.4"><circle cx="10" cy="10" r="6"/><path d="M15 15l5 5"/></svg></i></div>
<div class="abs usd">USD ▾</div>
<svg class="abs cart" width="30" height="28" viewBox="0 0 30 28" fill="none" stroke="#222" stroke-width="1.8"><path d="M1 3h5l4 15h15l3-11H8"/><circle cx="12" cy="23" r="2"/><circle cx="23" cy="23" r="2"/></svg>

<nav class="abs nav"><a>HOME</a><a>NEW BABY FORMULA</a><a>PRODUCTS</a><a>BLOG</a><a>CONTACT</a></nav>

<section class="abs hero" role="img" aria-label="Father feeding a baby with a bottle on a sofa, formula pouch beside them">
  <h1 class="h1a">CARING FOR YOUR LITTLE ONE,</h1>
  <h1 class="h1b">EVERY STEP OF THE WAY</h1>
  <a class="btn">Shop Now</a>
</section>

<div class="abs promo" style="left:111px;border-color:var(--green)">
  <div class="pic" role="img" aria-label="Infant formula pouch" style="background:linear-gradient(180deg,#eef0e4 0%,#c9d48c 60%,#8fa22c 100%)"></div>
  <div class="txt">INFANT FORMULA<br>MILK-BASED POWDER</div>
  <a class="btn">Shop Now</a>
</div>
<div class="abs promo" style="left:612px;border-color:var(--ink)">
  <div class="pic" role="img" aria-label="Formula container tin" style="background:linear-gradient(90deg,#e6e6e6,#fff,#e3e3e3)"></div>
  <div class="txt">INFANT FORMULA<br>MILK-BASED POWDER</div>
  <a class="btn">Shop Now</a>
</div>

<h2 class="abs title" style="top:1153px">FEATURED PRODUCTS</h2>
<div class="abs dots" style="top:1201px"><b></b><b></b></div>

<div class="abs card" style="left:111px;top:1289px"><div class="pic" role="img" aria-label="Formula powder with blue scoop" style="background:radial-gradient(ellipse at 45% 55%,#f1f1ee 0%,#e2e6ea 40%,#cfe6f3 60%,#fff 80%)"></div><hr><h3>LOREM LIPSUM</h3><p>$ 45.76</p></div>
<div class="abs card" style="left:358px;top:1289px"><div class="pic" role="img" aria-label="Pile of formula powder" style="background:radial-gradient(ellipse at 50% 60%,#e9dfd0 0%,#f2ece2 40%,#fff 75%)"></div><hr><h3>LOREM LIPSUM</h3><p>$ 66.98</p></div>
<div class="abs card" style="left:605px;top:1289px"><div class="pic" role="img" aria-label="Open tin with scoop" style="background:radial-gradient(circle at 50% 50%,#eef2f4 0%,#cfd6dc 45%,#b8c0c6 58%,#fff 72%)"></div><hr><h3>LOREM LIPSUM</h3><p>$ 98.56</p></div>
<div class="abs card" style="left:852px;top:1289px"><div class="pic" role="img" aria-label="Formula tin" style="background:radial-gradient(ellipse 70px 100px at 50% 52%,#dcdde0 0%,#f3f3f4 60%,#fff 100%)"></div><hr><h3>LOREM LIPSUM</h3><p>$ 56.87</p></div>
<div class="abs card" style="left:111px;top:1648px"><div class="pic" role="img" aria-label="Powder beside foil pack" style="background:linear-gradient(120deg,#fff 0%,#efe5cf 40%,#c9c9c9 75%,#9a9a9a 100%)"></div><hr><h3>LOREM LIPSUM</h3><p>$ 78.78</p></div>
<div class="abs card" style="left:358px;top:1648px"><div class="pic" role="img" aria-label="Small formula tin" style="background:radial-gradient(ellipse 55px 80px at 50% 50%,#ecebd6 0%,#f5f5f2 60%,#fff 100%)"></div><hr><h3>LOREM LIPSUM</h3><p>$ 67.12</p></div>
<div class="abs card" style="left:605px;top:1648px"><div class="pic" role="img" aria-label="Glass of milk and wooden spoon" style="background:linear-gradient(160deg,#fff 10%,#efe9df 40%,#b08a72 70%,#fff 95%)"></div><hr><h3>LOREM LIPSUM</h3><p>$ 98.34</p></div>
<div class="abs card" style="left:852px;top:1648px"><div class="pic" role="img" aria-label="Yellow scoop with powder" style="background:radial-gradient(ellipse at 50% 58%,#f3e3a0 0%,#f5f1e4 40%,#fff 75%)"></div><hr><h3>LOREM LIPSUM</h3><p>$ 23.43</p></div>

<section class="abs testi">
  <h2>OUR TESTIMONIALS</h2>
  <div class="abs dots"><b></b><b></b></div>
  <div class="quote" style="left:132px"><p>Lorem ipsum dolor sit amet, consectetur adipiscing elit, sed do eiusmod tempor incididunt ut labore et dolore magna aliqua.</p><div class="q">“</div><div class="av" role="img" aria-label="Customer portrait" style="background:#e9b58c"></div><div class="name">JOHN JAMES, LOREM LIPSUM</div></div>
  <div class="quote" style="left:630px"><p>Lorem ipsum dolor sit amet, consectetur adipiscing elit, sed do eiusmod tempor incididunt ut labore et dolore magna aliqua.</p><div class="q">“</div><div class="av" role="img" aria-label="Customer portrait" style="background:#4a5a6e"></div><div class="name">JOHN JAMES, LOREM LIPSUM</div></div>
</section>
<div class="pager"><i></i><i></i><i></i></div>

<h2 class="abs title" style="top:2823px">OUR RECENT POSTS</h2>
<div class="abs dots" style="top:2871px"><b></b><b></b></div>

<article class="abs post" style="left:111px"><div class="pic" role="img" aria-label="Formula powder in a scoop" style="background:linear-gradient(135deg,#f1f0ea,#dcdad0)"></div><div class="date">09<small>JAN</small></div><h4>Lorem ipsum dolor sit amet</h4><p>Lorem ipsum dolor sit amet, consectetur adipiscing elit, sed do eiusmod tempor</p><a class="btn">Read More</a></article>
<article class="abs post" style="left:445px"><div class="pic" role="img" aria-label="Open formula tin with blue scoop" style="background:linear-gradient(135deg,#d9a56e,#b8bcc8 55%,#e8e8e8)"></div><div class="date">09<small>JAN</small></div><h4>Lorem ipsum dolor sit amet</h4><p>Lorem ipsum dolor sit amet, consectetur adipiscing elit, sed do eiusmod tempor</p><a class="btn">Read More</a></article>
<article class="abs post" style="left:779px"><div class="pic" role="img" aria-label="Bottle and formula tin on a kitchen counter" style="background:linear-gradient(135deg,#d94b3c,#ece7df 50%,#cfcac0)"></div><div class="date">09<small>JAN</small></div><h4>Lorem ipsum dolor sit amet</h4><p>Lorem ipsum dolor sit amet, consectetur adipiscing elit, sed do eiusmod tempor</p><a class="btn">Read More</a></article>

<section class="abs feat">
  <div class="f" style="left:106px"><svg width="52" height="48" viewBox="0 0 52 48" fill="none" stroke="#9fb338" stroke-width="2"><rect x="2" y="14" width="30" height="22"/><path d="M32 20h10l8 8v8H32"/><circle cx="12" cy="40" r="4"/><circle cx="40" cy="40" r="4"/></svg><div><h5>FREE SHIPPING</h5><p>Free Shipping on all orders</p></div></div>
  <div class="f" style="left:448px"><svg width="46" height="46" viewBox="0 0 46 46" fill="none" stroke="#9fb338" stroke-width="2"><circle cx="23" cy="23" r="20"/><circle cx="23" cy="23" r="12"/><path d="M23 16v14M19 19h6a2 2 0 0 1 0 4h-4a2 2 0 0 0 0 4h6"/></svg><div><h5>MONEY GUARANTEE</h5><p>We are guarantee to your money</p></div></div>
  <div class="f" style="left:820px"><svg width="54" height="50" viewBox="0 0 54 50" fill="none" stroke="#9fb338" stroke-width="2"><circle cx="34" cy="16" r="9"/><circle cx="34" cy="16" r="4"/><path d="M2 32h10l8 4h10a3 3 0 0 1 0 6H18M12 44l14 4 24-12"/></svg><div><h5>PREMIUM SUPPORT</h5><p>24 Hour online support</p></div></div>
</section>

<footer class="abs footer">
  <div class="col" style="left:105px"><h6>MY ACCOUNT</h6><ul><li>Request-for-a-quote</li><li>Terms &amp; Conditions</li><li>Refund Policy</li><li>Privacy Policy</li><li>Contact</li></ul></div>
  <div class="col" style="left:380px"><h6>INFORMATION</h6><ul><li>My account</li><li>Checkout</li><li>Cart</li><li>Wishlist</li><li>Contact</li></ul></div>
  <div class="col" style="left:645px"><h6>LINKS</h6><ul><li>Home</li><li>Shop</li><li>Products</li><li>Contact</li></ul></div>
  <div class="col" style="left:833px"><h6>CONTACT US</h6><ul>
    <li><span class="ic"><svg width="16" height="16" viewBox="0 0 24 24" fill="#fff"><path d="M6 2l4 4-2 3c1 3 4 6 7 7l3-2 4 4-3 4C10 21 3 14 2 5z"/></svg></span>+1 888 888 8888</li>
    <li><span class="ic"><svg width="16" height="12" viewBox="0 0 24 18" fill="none" stroke="#fff" stroke-width="2"><rect x="1" y="1" width="22" height="16"/><path d="M1 1l11 9 11-9"/></svg></span>care@nestlingbaby.com</li>
    <li><span class="ic"><svg width="14" height="18" viewBox="0 0 14 18" fill="#fff"><path d="M7 0a7 7 0 0 1 7 7c0 5-7 11-7 11S0 12 0 7a7 7 0 0 1 7-7zm0 4a3 3 0 1 0 0 6 3 3 0 0 0 0-6z"/></svg></span>7890 lorem lipsum sit amet</li>
    <li><span class="ic"></span>902 789</li></ul></div>
</footer>
<div class="abs totop"><svg width="18" height="18" viewBox="0 0 24 24" fill="none" stroke="#9fb338" stroke-width="3"><path d="M12 20V5M5 11l7-7 7 7"/></svg></div>

<div class="abs copy">COPYRIGHT © 2024, ALL RIGHTS RESERVED</div>
</body>
</html>
```